Company Website for Varnoth Signal, an open source data analytics company focused on relationship and li

I need a company/brand website for our new startup, Varnoth Signal LLC. We are a company focused on using life pattern analysis techniques, looking at relationships and how relationships, attributes, and activity cluster to infer aggregate information about individuals and groups. Our focus is on improving the digital advertising market.

We have a company logo which I will upload shortly.

Target Market(s)

Digital Advertising

Number of Pages Required

3 page

Font styles to use
Sans Serif

Requirements
Must have
• An main page, about us, contact page.
Nice to have
• Varnoth Signal relies on state of the art analytics applied to a the digital marketing space. While it is heavy in science, we also understand the art of influence. The website should have a scientific edge but also a flair that illustrates our focus on applying the hard science and analytics to influencing the behavior of people.

```html
<!DOCTYPE html>
<html lang="en">
<head>
<meta charset="utf-8">
<title>Varnoth Signal</title>
<link href="https://fonts.googleapis.com/css2?family=Montserrat:wght@400;500;600;700&display=swap" rel="stylesheet">
<style>
:root{
  --blue:#1f73c4;
  --blue-light:#3b8fe0;
  --dark:#1e1e1e;
  --darker:#191919;
  --bar:#232323;
  --footer:#262626;
  --text:#d8d8d8;
  --muted:#b9b9b9;
  --white:#ffffff;
}
*{margin:0;padding:0;box-sizing:border-box}
html,body{width:741px;height:1200px;overflow:hidden;background:var(--dark)}
body{font-family:"Montserrat",sans-serif;color:var(--white);position:relative}
.abs{position:absolute}
.hero{left:0;top:0;width:741px;height:403px;background:linear-gradient(160deg,#4a3b2f 0%,#3a2e25 45%,#2b231d 100%)}
.hero-shade{left:0;top:0;width:741px;height:403px;background:rgba(20,18,16,.45)}
.brand{left:72px;top:14px;display:flex;align-items:center;gap:6px;font-weight:700;font-size:14px;color:var(--blue-light)}
.brand i{width:10px;height:10px;border-radius:50%;background:#f39c12;display:block}
.nav{top:21px;left:366px;display:flex;gap:13px;font-size:7.5px;font-weight:500}
.nav span.active{color:var(--blue-light);border-bottom:1px solid var(--blue-light);padding-bottom:3px}
.nav-icon{top:21px;width:11px;height:11px;border-radius:50%}
.tagline{left:74px;top:155px;width:344px;height:36px;border:2px solid var(--white);font-size:16.5px;font-weight:700;display:flex;align-items:center;justify-content:center;letter-spacing:.2px}
.headline{left:72px;top:194px;font-size:29px;font-weight:700;line-height:39px;letter-spacing:.3px}
.cta{left:74px;top:276px;width:108px;height:26px;background:var(--blue);font-size:9.5px;font-weight:700;letter-spacing:1px;display:flex;align-items:center;justify-content:center}
.cta-tip{left:74px;top:302px;width:0;height:0;border-top:7px solid var(--blue);border-right:8px solid transparent}
.dot{top:357px;width:7px;height:7px;border-radius:50%;background:var(--white)}
.section-title{left:0;top:403px;width:741px;height:64px;background:var(--dark);font-size:24.5px;font-weight:500;letter-spacing:.8px;display:flex;align-items:center;justify-content:center}
.tabs{left:0;top:467px;width:741px;height:32px;background:var(--darker);border-top:1px solid #2c2c2c;border-bottom:1px solid #2c2c2c}
.tab{top:0;height:32px;font-size:7.5px;font-weight:500;display:flex;align-items:center;justify-content:center;border-left:1px solid #333}
.story{left:0;top:499px;width:741px;height:283px;background:var(--dark)}
.story-img{left:69px;top:532px;width:293px;height:100px;background:linear-gradient(135deg,#f4f6f8,#dfe6ee)}
.story-head{left:69px;top:645px;font-size:17.5px;font-weight:500;letter-spacing:.3px}
.story-text{left:70px;top:672px;width:292px;font-size:6.2px;line-height:12.3px;color:var(--text)}
.num{left:377px;width:36px;height:36px;border-radius:50%;background:var(--blue);font-size:17px;display:flex;align-items:center;justify-content:center}
.point{left:428px;width:240px}
.point h3{font-size:7px;font-weight:500;color:var(--blue-light);margin-bottom:5px}
.point p{font-size:6px;line-height:12.3px;color:var(--text)}
.services{left:0;top:782px;width:741px;height:281px;background:linear-gradient(135deg,#3a86cf,#2a72bb 60%,#3b7dc0)}
.card{top:861px;width:120px;height:120px;border:1px solid rgba(255,255,255,.85);display:flex;align-items:center;justify-content:center}
.label{top:993px;width:70px;height:24px;border:1.5px solid var(--white);font-size:7.5px;font-weight:600;letter-spacing:.6px;display:flex;align-items:center;justify-content:center}
.footer{left:0;top:1063px;width:741px;height:110px;background:var(--footer)}
.fcol{top:1093px;font-size:6.2px;line-height:12.5px;font-weight:600}
.fcol h4{font-size:7px;font-weight:500;color:var(--blue-light);margin-bottom:6px}
.accent{color:var(--blue-light)}
.social{top:1127px;width:17px;height:17px;border-radius:50%;border:1px solid #555}
.subscribe{left:481px;top:1141px;width:89px;height:16px;border:1px solid #555;border-radius:9px;font-size:6px;color:#888;padding-left:9px;display:flex;align-items:center}
.bottom{left:0;top:1173px;width:741px;height:27px;background:#1c1c1c}
</style>
</head>
<body>
<div class="abs hero" role="img" aria-label="Overhead photo of colleagues with laptops and tablets around a wooden table"></div>
<div class="abs hero-shade"></div>

<div class="abs brand"><i></i>Varnoth Signal</div>
<nav class="abs nav"><span class="active">Home</span><span>About us</span><span>Our Team</span><span>Our Products</span><span>Blog</span><span>Contact</span></nav>
<div class="abs nav-icon" style="left:638px;background:var(--blue)"></div>
<div class="abs nav-icon" style="left:654px;background:#555"></div>

<svg class="abs" style="left:24px;top:201px" width="14" height="18" viewBox="0 0 14 18"><path d="M10 2 3 9l7 7" fill="none" stroke="#fff" stroke-width="2.5"/></svg>
<svg class="abs" style="left:697px;top:201px" width="14" height="18" viewBox="0 0 14 18"><path d="M4 2l7 7-7 7" fill="none" stroke="#fff" stroke-width="2.5"/></svg>

<div class="abs tagline">BECAUSE YOUR TIME IS VALUABLE</div>
<div class="abs headline">TAP INTO THE POWER OF<br>SOCIAL MEDIA.</div>
<div class="abs cta">OUR PRODUCTS</div>
<div class="abs cta-tip"></div>

<div class="abs dot" style="left:352px;background:var(--blue-light)"></div>
<div class="abs dot" style="left:362px"></div>
<div class="abs dot" style="left:372px"></div>

<svg class="abs" style="left:346px;top:384px" width="40" height="20" viewBox="0 0 40 20"><path d="M0 20 20 0l20 20z" fill="var(--blue)"/><path d="M16 12l4 3 4-3" fill="none" stroke="#fff" stroke-width="1"/></svg>

<div class="abs section-title">WHY WE ARE DIFFERENT</div>

<div class="abs tabs">
  <div class="abs tab" style="left:68px;width:83px">Our Story</div>
  <div class="abs tab" style="left:151px;width:69px">Mission &amp; Vision</div>
  <div class="abs tab" style="left:220px;width:71px;border-right:1px solid #333">Company Values</div>
</div>

<div class="abs story"></div>
<div class="abs story-img" role="img" aria-label="Illustration of a social network of connected user profiles"></div>
<div class="abs story-head">DIGITAL ADVERTISING MARKET</div>
<p class="abs story-text">Lorem ipsum dolor sit amet, consectetur adipiscing elit. Aenean egestas eu leo nec eleifend. Nulla sapien turpis, convallis ac ultrices sed, aliquam sit amet arcu. Phasellus est orci, bibendum consequat quam sit amet, facilisis pharetra nisl. Nullam ultrices mi quam, et volutpat magna suscipit eget.</p>

<div class="abs num" style="top:531px">1</div>
<div class="abs point" style="top:534px"><h3>DUMMY TEXT OF THE PRINTING AND TYPESETTING</h3><p>Consectetur adipiscing elit. Pellentesque ut mollis lectus. Ut ultricies lacinia feugiat. Cras sed enim quis nunc condimentum ullamcorper. Aliquam eget lorem at purus porta volutpat in in enim. Fusce sollicitudin pulvinar rutrum. Etiam tempus porta mauris at fermentum.</p></div>
<div class="abs num" style="top:615px">2</div>
<div class="abs point" style="top:617px"><h3>DUMMY TEXT OF THE PRINTING AND TYPESETTING</h3><p>Consectetur adipiscing elit. Pellentesque ut mollis lectus. Ut ultricies lacinia feugiat. Cras sed enim quis nunc condimentum ullamcorper. Aliquam eget lorem at purus porta volutpat in in enim.</p></div>
<div class="abs num" style="top:693px">3</div>
<div class="abs point" style="top:695px"><h3>DUMMY TEXT OF THE PRINTING AND TYPESETTING</h3><p>Consectetur adipiscing elit. Pellentesque ut mollis lectus. Ut ultricies lacinia feugiat. Cras sed enim quis nunc condimentum ullamcorper. Aliquam eget lorem at purus porta volutpat in in enim.</p></div>

<div class="abs services" role="img" aria-label="Blue tinted photo of a team reviewing charts and documents"></div>

<div class="abs card" style="left:89px"><svg width="52" height="44" viewBox="0 0 52 44" fill="none" stroke="#fff" stroke-width="2.5"><path d="M26 3 49 14 26 25 3 14z"/><path d="M3 22l23 11 23-11"/><path d="M3 30l23 11 23-11"/></svg></div>
<div class="abs card" style="left:233px"><svg width="56" height="48" viewBox="0 0 56 48" fill="none" stroke="#fff" stroke-width="2.5"><rect x="4" y="26" width="7" height="16" fill="#fff"/><rect x="14" y="18" width="7" height="24" fill="#fff"/><path d="M2 44h30"/><circle cx="35" cy="30" r="9"/><path d="M41 37l8 8"/><path d="M10 14l10-6 8 5 12-10" stroke-width="2"/><path d="M36 3h5v5" stroke-width="2"/></svg></div>
<div class="abs card" style="left:383px"><svg width="54" height="44" viewBox="0 0 54 44" fill="none" stroke="#fff" stroke-width="3"><path d="M17 34H13a10 10 0 0 1 0-20 14 14 0 0 1 27-2 10 10 0 0 1 2 22h-5"/><path d="M27 20v12"/><circle cx="27" cy="38" r="1.8" fill="#fff"/></svg></div>
<div class="abs card" style="left:532px"><svg width="52" height="48" viewBox="0 0 52 48" fill="#fff"><circle cx="14" cy="19" r="5"/><path d="M5 34c0-6 4-9 9-9s9 3 9 9z"/><circle cx="38" cy="19" r="5"/><path d="M29 34c0-6 4-9 9-9s9 3 9 9z"/><path d="M12 9a17 17 0 0 1 27 0" fill="none" stroke="#fff" stroke-width="2"/><path d="M40 40a17 17 0 0 1-27 0" fill="none" stroke="#fff" stroke-width="2"/><path d="M36 5l4 4-5 2z"/><path d="M16 43l-4-4 5-2z"/></svg></div>

<div class="abs label" style="left:115px">DATA</div>
<div class="abs label" style="left:258px">ANANLYTICS</div>
<div class="abs label" style="left:408px">RISK</div>
<div class="abs label" style="left:557px">INFLUENCE</div>

<div class="abs footer"></div>
<div class="abs fcol" style="left:69px">Copyright 2017-18 <span class="accent">Varnoth Signal</span></div>
<div class="abs social" style="left:70px"></div>
<div class="abs social" style="left:93px"></div>
<div class="abs social" style="left:116px"></div>
<div class="abs social" style="left:139px"></div>

<div class="abs fcol" style="left:275px;top:1091px;line-height:8px"><h4>Our location</h4>Kestrel Row Offices 0000 Aldmere,<br>Suite 118 Pinecrest, IL 00000<div style="margin-top:5px;line-height:12.5px">Phone : +00 1 98765432<br>Email : info@varnothsignal.com</div></div>

<div class="abs fcol" style="left:481px;top:1091px;width:200px"><h4>Kepp in touch</h4>Lorem ipsum dolor sit amet, consectetur adi sollicitud ante tellus ornare mi, et mollis</div>
<div class="abs subscribe">Your email</div>
<svg class="abs" style="left:556px;top:1145px" width="8" height="8" viewBox="0 0 8 8"><path d="M0 4h7M4 1l3 3-3 3" fill="none" stroke="#999" stroke-width="1.2"/></svg>

<div class="abs bottom"></div>
<svg class="abs" style="left:364px;top:1183px" width="12" height="8" viewBox="0 0 12 8"><path d="M1 7l5-5 5 5" fill="none" stroke="#fff" stroke-width="2"/></svg>
</body>
</html>
```